Wine Label Design-Hollow Creek Vineyard

Hollow Creek Vineyard is in the Barossa Valley in South Australia. The Barossa is recognized as Australia's premier wine region, producing Australia's icon wines and some " new takes on traditional".
This family owned and operated vineyard grows some exceptionally high quality fruit. Most of the fruit is sold and used for some of Australia's most iconic wines. Small quantities are retained by the owners for some wines with very limited availability. (Wines were previously sold as Brackwell Vineyards Hollow Creek ( Shiraz, Cabernet etc).

The wines will in the future be labeled simply ‘Hollow Creek Vineyard’. The label will launch this new identity for the single family single vineyard and its high quality wines which are a true expression of the vineyard and derive from the Hollow Creek common to this ancient area (800-2000 million years old).
The label should reflect
• Single vineyard, family owned
• vines in very old rock & soils
• High quality & reliability
• Edgy but true, design based thinking (Please note:blue is generally seen as an unacceptable colour for a wine label?? Don’t ask me why)

The wines will be sold mostly direct in Australia ( ie not through retail stores), with limited export to Asia, Scandinavia and Canada.
There are three quality levels and price points in the portfolio
1. Entry level premium for everyday drinking for discriminating drinkers-approx AUD20
2. Super Premium-approx AUD30
3. Limited Release ultlra premium-AUD75-90?
We envisage three variations on the label but with an obvious & common design element. This design element should be able to be used for corporate identification and promotion
The paper stock will be waterproof and self adhesive. Our preference is for designs that engage the user by appealing to both sight and touch. It is preferred that textures be added eg embossing, high build varnish etc-rather than be a facet of the stock itself.
For information on statutory label requirements refer to www.vintnerregistry-example.com . In brief
o Front label need not show any mandatory information. However we would prefer Variety, Barossa Valley, Year and alcohol to be shown on the front label
o Back label should show all mandatories and allow for a bar code
Updates

Project Deadline Extended
Reason: I've had a problem with my wireless broadband account and reception has been intermittent to say the least to the extent that I switched off at the weekend. Just going downtown now for a 'polite discussion' with my service provider.

Project Deadline Extended
Reason: I have receiver insufficient designs of quality which we would consider. Too many designs have a "cut and paste" appearance - too few exhibit an original art/design element which truly identifies the product.

Gals & Guys

most of the designs submitted lack punch and originality and are totally unmemorable.
Please-get on Searcho or whatever enter "Wine Label Designs" and do some research b4 u waste your time and mine. Formulaic cut and paste will not win the day. That's not to say that cut and paste can't work-but it must have some originality, impact and command attention. Please surprise me.

Following on from a question from a designer about who is our competition and what we are looking for I sent the following 
"I don't think I can add anything new. Read the brief and comments again and research wine labels on the web. In 30 minutes you'll get a good idea of the creative edgy designs in the industry. There are a plethora of collections. Our competition-anyone with a label. In 2010 there were over 2400 "producers" in other words 2400 producers with at least one label. In fact there are over 25000 Australian wines and then the numerous imported wines.

Target Market(s)

$20 people who budget everyday but have graduated from drinking 'entry level' wines. These people will likely fit into Cat. (b) in the $30 wine

$30 (a) will not over-compromise on some everyday discretionary expenditure.(b) might buy for special occasions

$70-$90 Professional/successful people with high disposable/discretionary income not particularly worried about recession. wine geeks.

Industry/Entity Type

Retail

Requirements
Must have
• identifiable element across range of wines

```html
<!DOCTYPE html>
<html lang="en">
<head>
<meta charset="utf-8">
<title>Hollow Creek Vineyard – Wine Label</title>
<link rel="stylesheet" href="https://fonts.googleapis.com/css2?family=Delius&family=Tinos:wght@700&display=swap">
<style>
  :root {
    --page: #ffffff;
    --board-light: #eef1f3;
    --board-mid: #8fa2a6;
    --board-dark: #1a2324;
    --label-green: #5ef55e;
    --label-edge: #2bf02b;
    --band-tan: #c49a5e;
    --ink: #111111;
    --art-orange: #f0552e;
    --art-brown: #4a3a30;
    --ghost: rgba(60, 70, 72, 0.28);
    --white: #ffffff;
  }
  * { box-sizing: border-box; margin: 0; padding: 0; }
  html, body {
    width: 1200px; height: 951px; overflow: hidden;
    background: var(--page);
  }
  .canvas { position: relative; width: 1200px; height: 951px; }
  .board {
    position: absolute; left: 53px; top: 52px; width: 1100px; height: 841px;
    background: linear-gradient(150deg, var(--board-light) 0%, var(--board-mid) 50%, var(--board-dark) 100%);
    border: 1px solid #c9cfd1;
  }
  .ghost-motif {
    position: absolute; left: 415px; top: 125px; width: 305px; height: 535px;
    background: radial-gradient(ellipse closest-side at center, var(--ghost) 0%, rgba(60,70,72,0.12) 60%, rgba(60,70,72,0) 100%);
  }

  /* brand mark */
  .brand-mark { position: absolute; left: 527px; top: 101px; display: flex; align-items: center; gap: 6px; }
  .brand-mark__square { width: 20px; height: 78px; background: var(--label-green); border: 2px solid var(--label-edge); }
  .brand-mark__name {
    font-family: "Delius", cursive; font-size: 20px; line-height: 1.1; color: var(--ink);
  }

  /* labels */
  .label {
    position: absolute; background: var(--label-green);
    border: 4px solid var(--label-edge);
    font-family: "Delius", cursive; color: var(--ink);
    overflow: hidden;
  }
  .label--front { left: 247px; top: 243px; width: 315px; height: 477px; }
  .label--back  { left: 677px; top: 258px; width: 284px; height: 431px; text-align: center; }

  .front__band { position: absolute; left: 0; right: 0; top: 202px; height: 70px; background: var(--band-tan); }
  .front__art {
    position: absolute; left: 24px; top: 118px; width: 200px; height: 170px;
    background: radial-gradient(ellipse closest-side at center, var(--art-orange) 0%, var(--art-brown) 70%, rgba(74,58,48,0) 100%);
  }
  .front__vineyard {
    position: absolute; right: 12px; top: 18px; text-align: right;
    font-size: 28px; font-weight: 400; line-height: 1.2;
  }
  .front__wine {
    position: absolute; right: 12px; top: 280px; text-align: right;
    font-size: 28px; line-height: 1.2;
  }
  .front__volume { position: absolute; left: 10px; bottom: 28px; font-size: 19px; }
  .front__alcohol { position: absolute; right: 14px; bottom: 16px; text-align: right; font-size: 19px; line-height: 1.2; }

  .back__block { position: absolute; left: 0; right: 0; }
  .back__title { top: 6px; font-size: 14.5px; font-weight: 400; line-height: 1.25; }
  .back__story {
    top: 54px; left: 10px; right: 10px;
    font-family: "Tinos", serif; font-weight: 700;
    font-size: 10.4px; line-height: 1.33;
  }
  .back__drinks { top: 178px; font-family: "Tinos", serif; font-weight: 700; font-size: 10.4px; }
  .back__statements { top: 200px; font-size: 14.5px; line-height: 1.2; }
  .back__barcode-space {
    top: 260px; left: 58px; right: auto; width: 160px; height: 86px;
    background: var(--white); border: 2px solid var(--ink);
  }
  .back__address { top: 352px; font-size: 13.5px; line-height: 1.16; }
</style>
</head>
<body>
<main class="canvas">
  <div class="board">
    <div class="ghost-motif" role="img" aria-label="Large faint butterfly motif in grey behind the labels"></div>
  </div>

  <div class="brand-mark">
    <span class="brand-mark__square"></span>
    <span class="brand-mark__name">Hollow Creek<br>Vineyard</span>
  </div>

  <section class="label label--front" aria-label="Front label">
    <div class="front__band"></div>
    <div class="front__art" role="img" aria-label="Illustration of an orange and brown butterfly resting on a pale green wine glass outline"></div>
    <h1 class="front__vineyard">Hollow Creek<br>Vineyard</h1>
    <p class="front__wine">Barossa Valley<br>Bordeaux<br>2012</p>
    <p class="front__volume">750 ml</p>
    <p class="front__alcohol">13.50%<br>Alc/Vol</p>
  </section>

  <section class="label label--back" aria-label="Back label">
    <h2 class="back__block back__title">Barossa Valley Bordeaux<br>2012</h2>
    <p class="back__block back__story">Our Wines are planted on areas which are charecterized by enourmous quantities of shattered shale, slate and limestone based rock, which are major componants in our unique flavor and tight structure and minerality with abundant and generous fruit. Our wines deink well from the release and get better from 2 to 12 years.</p>
    <p class="back__block back__drinks">8.3 Standard Drinks</p>
    <p class="back__block back__statements">Wine of Australia<br>Contains sulfates<br>Produced with milk products.</p>
    <div class="back__block back__barcode-space"></div>
    <p class="back__block back__address">Hollow Creek Vineyard<br>Lot 3 Fernhill Drive<br>Elmbrook, SA<br>5999 Australia</p>
  </section>
</main>
</body>
</html>
```